Halvex Power

We need a business card for "Halvex power". I have uploaded the logo, the color of the card should be according to the logo "Blackish".
Basically halvex power is a solar company.
Also we would like a sample file in which we can edit the information such names and contact details ourselves
The card would be two sided with following details
1- logo on front and underneath the logo there should be a line saying
"Cleaner . Cheaper . Power"
2-website i.e "www.halvexpowerco.com"
3- Icons for Facebook and Instagram that tells the clients we are available on both social sites.
4- name of the person with his/her designation underneath and email address
5-contact number
6- 1-800--- number with the extension number

its up to the designer how he/she places the details,but it must look professional

Industry/Entity Type

Business

Contact Information for Business Card

5-contact number

Requirements
Must have
• 1- logo on front and underneath the logo there should be a line saying
• "Cleaner . Cheaper . Power"
• 2-website i.e "www.halvexpowerco.com"
• 3- Icons for Facebook and Instagram that tells the clients we are available on both social sites.
• 4- name of the person with his/her designation underneath and email address
• 5-contact number of the person
• 6- 1-800--- number with the extension number
• 7-card should be in black shade like the logo

```html
<!DOCTYPE html>
<html lang="en">
<head>
<meta charset="utf-8">
<title>Halvex Power – Business Card</title>
<link href="https://fonts.googleapis.com/css2?family=Raleway:wght@400;500;600&display=swap" rel="stylesheet">
<style>
  :root {
    --stage: #1f2225;
    --card-dark: #2c343c;
    --card-dark-2: #46525c;
    --card-light: #ffffff;
    --green: #7dc242;
    --charcoal: #4a4b4d;
    --ink: #3a3a3a;
    --muted: #8a8a8a;
    --soft-white: #d9dee2;
  }
  * { box-sizing: border-box; margin: 0; padding: 0; }
  html, body { width: 1200px; height: 738px; overflow: hidden; }
  body {
    background: var(--stage);
    font-family: "Raleway", sans-serif;
    position: relative;
  }
  .card {
    position: absolute;
    top: 219px;
    width: 520px;
    height: 300px;
    overflow: hidden;
  }
  /* Front */
  .card-front { left: 50px; background: var(--card-dark); }
  .front-backdrop {
    position: absolute; inset: 0;
    background: linear-gradient(160deg, var(--card-dark-2) 0%, var(--card-dark) 55%, #232a31 100%);
  }
  .front-brand {
    position: absolute; left: 0; right: 0; top: 104px;
    text-align: center;
    color: var(--green);
    font-weight: 600; font-size: 34px; letter-spacing: 1px;
  }
  .front-tagline {
    position: absolute; left: 0; right: 0; top: 154px;
    text-align: center;
    color: var(--soft-white);
    font-size: 12px; font-weight: 500; letter-spacing: 2px;
  }
  .front-social {
    position: absolute; left: 0; right: 0; top: 238px;
    display: flex; justify-content: center; align-items: center; gap: 10px;
    color: #ffffff; font-size: 13px; font-weight: 500;
  }
  .social-dot { width: 14px; height: 14px; border-radius: 50%; background: #ffffff; }
  /* Back */
  .card-back { left: 630px; background: var(--card-light); }
  .back-brand {
    position: absolute; left: 30px; top: 34px;
    color: var(--green); font-weight: 600; font-size: 26px;
  }
  .holder {
    position: absolute; right: 30px; top: 100px; text-align: right;
  }
  .holder-name { color: var(--green); font-size: 24px; font-weight: 500; letter-spacing: .5px; }
  .holder-title { color: var(--muted); font-size: 12px; margin-top: 6px; }
  .rule-name { position: absolute; left: 150px; right: 30px; top: 134px; height: 2px; background: var(--green); }
  .rule-contact { position: absolute; left: 34px; width: 200px; top: 176px; height: 2px; background: var(--green); }
  .contacts {
    position: absolute; left: 34px; top: 186px; list-style: none;
    color: var(--ink); font-size: 13.5px; line-height: 17px;
  }
  .contacts li { display: flex; align-items: center; gap: 8px; }
  .contacts svg { width: 10px; height: 10px; flex: none; }
  .contacts .accent { color: var(--green); }
  .bands { position: absolute; left: 0; top: 0; }
  .address {
    position: absolute; right: 20px; top: 246px; text-align: right;
    color: #ffffff; font-size: 12px; line-height: 17px;
  }
</style>
</head>
<body>

<section class="card card-front">
  <div class="front-backdrop" role="img" aria-label="Softly blurred office interior photograph in dark blue-grey tones"></div>
  <div class="front-brand">Halvex Power</div>
  <div class="front-tagline">Cleaner . Cheaper . Power</div>
  <div class="front-social">
    <span class="social-dot"></span>
    <span class="social-dot"></span>
    <span>1-800</span>
  </div>
</section>

<section class="card card-back">
  <svg class="bands" width="520" height="300" viewBox="0 0 520 300">
    <polygon points="0,282 300,282 313,266 0,266" fill="var(--green)"/>
    <polygon points="0,282 300,282 286,300 0,300" fill="var(--green)" opacity=".85"/>
    <polygon points="320,226 520,226 520,300 264,300" fill="var(--charcoal)"/>
  </svg>
  <div class="back-brand">Halvex Power</div>
  <div class="holder">
    <div class="holder-name">DARRIN MOTT</div>
    <div class="holder-title">President</div>
  </div>
  <div class="rule-name"></div>
  <div class="rule-contact"></div>
  <ul class="contacts">
    <li><svg viewBox="0 0 10 10"><path d="M2 1l2 2-1 1.5c.8 1.5 1.5 2.2 3 3L7.5 6l2 2-1.5 1.5C4 9 1 6 .5 1.5z" fill="var(--green)"/></svg><span>1-844-HXSOLAR</span></li>
    <li><svg viewBox="0 0 10 10"><rect x="2.5" y=".5" width="5" height="9" rx="1" fill="none" stroke="var(--green)"/></svg><span>1-844-555-0192</span></li>
    <li><svg viewBox="0 0 10 10"><rect x=".5" y="2" width="9" height="6" fill="none" stroke="var(--green)"/><path d="M.5 2l4.5 3.5L9.5 2" fill="none" stroke="var(--green)"/></svg><span>info@halvexpowerco.com</span></li>
    <li><svg viewBox="0 0 10 10"><circle cx="5" cy="5" r="4.3" fill="none" stroke="var(--green)"/><path d="M.7 5h8.6M5 .7c-2.5 2.8-2.5 5.8 0 8.6M5 .7c2.5 2.8 2.5 5.8 0 8.6" fill="none" stroke="var(--green)" stroke-width=".8"/></svg><span>www.<span class="accent">halvexpowerco</span>.com</span></li>
  </ul>
  <div class="address">14 Ridgeline Commerce Way<br>Alder Flats T0C 2K9</div>
</section>

</body>
</html>
```